co working space / serviced office/ business centre

Brevlo - brevlo.in, is a very young brand bieng run by 3 young entrepreneurs. We want to be become out of the league company delivering fabulous and beautiful serviced offices in India and abroad. We hire designers who have made spaces across the world. We want to get visiting card design which gives complete fresh look to the people who carries that card, has to be very impactful and should symbolise happy young and energetic brand. should be completely out of the box thinking of international level, should portray global brand image.

Target Market(s)

Startups, (Small, medium and large corporates)

Industry/Entity Type

Business

Contact Information for Business Card

Name, Email, Address, Mobile number, Landline number, website

Colors

Designer to choose colors to be used in the design.

Requirements
Must have
• Nice new shape
Nice to have
• We want creative cuts, different size and impactful brand clarity
Should not have
• Boring and regular design and shape

```html
<!DOCTYPE html>
<html lang="en">
<head>
<meta charset="utf-8">
<title>Brevlo Business Card</title>
<link href="https://fonts.googleapis.com/css2?family=Open+Sans:wght@400;600;700&family=Montserrat:wght@800&display=swap" rel="stylesheet">
<style>
  :root {
    --brand-red: #e8313a;
    --ink: #1a1a1a;
    --muted: #555555;
    --card: #ffffff;
    --backdrop: #3a3a3a;
  }
  * { margin: 0; padding: 0; box-sizing: border-box; }
  html, body { width: 1200px; height: 864px; overflow: hidden; }
  body {
    background: var(--backdrop);
    font-family: "Open Sans", sans-serif;
    position: relative;
  }
  .card {
    position: absolute;
    width: 560px;
    height: 320px;
    background: var(--card);
    overflow: hidden;
    box-shadow: 0 10px 30px rgba(0,0,0,.45);
  }
  .card--front { left: 60px; top: 80px; }
  .card--back { left: 580px; top: 464px; }

  .wordmark {
    display: flex; align-items: center; gap: 12px;
    color: var(--brand-red);
    font-family: "Montserrat", sans-serif;
    font-weight: 800;
    letter-spacing: 3px;
  }
  .wordmark__dot {
    width: 22px; height: 22px; border-radius: 50%;
    background: var(--brand-red);
  }
  .wordmark-rule { height: 3px; background: var(--brand-red); }

  .card--front .brand {
    position: absolute; left: 0; right: 0; top: 98px;
    display: flex; flex-direction: column; align-items: center;
  }
  .card--front .wordmark { font-size: 56px; }
  .card--front .wordmark-rule { width: 330px; margin-top: 8px; }
  .card--front .site {
    position: absolute; left: 0; right: 0; top: 238px;
    text-align: center; font-size: 17px; font-weight: 600; color: var(--ink);
  }

  .card--back .brand { position: absolute; left: 40px; top: 36px; }
  .card--back .wordmark { font-size: 38px; gap: 9px; }
  .card--back .wordmark__dot { width: 16px; height: 16px; }
  .card--back .wordmark-rule { width: 240px; margin-top: 6px; }

  .person { position: absolute; left: 40px; top: 150px; }
  .person__name { color: var(--brand-red); font-size: 22px; font-weight: 700; line-height: 1.1; }
  .person__role { color: var(--muted); font-size: 15px; }

  .divider { position: absolute; height: 1px; background: var(--ink); }
  .divider--left { left: 40px; top: 206px; width: 200px; }
  .divider--right { right: 40px; top: 120px; width: 230px; }

  .contacts { position: absolute; left: 40px; top: 216px; list-style: none; }
  .contacts li {
    display: flex; align-items: center; gap: 8px;
    font-size: 15px; color: var(--ink); line-height: 22px;
  }
  .contacts svg { width: 12px; height: 12px; fill: var(--brand-red); }

  .address {
    position: absolute; right: 40px; top: 128px;
    text-align: right; font-size: 14px; color: var(--muted); line-height: 19px;
  }
  .band { position: absolute; left: 0; bottom: 0; width: 560px; height: 100px; }
  .band__site {
    position: absolute; right: 30px; bottom: 40px;
    color: #fff; font-size: 15px; font-weight: 600;
  }
</style>
</head>
<body>
  <section class="card card--front" aria-label="Card front">
    <div class="brand">
      <div class="wordmark"><span class="wordmark__dot"></span>BREVLO</div>
      <div class="wordmark-rule"></div>
    </div>
    <p class="site">www.brevlo.in</p>
  </section>

  <section class="card card--back" aria-label="Card back">
    <div class="brand">
      <div class="wordmark"><span class="wordmark__dot"></span>BREVLO</div>
      <div class="wordmark-rule"></div>
    </div>

    <div class="person">
      <p class="person__name">Ravi Kapoor</p>
      <p class="person__role">President</p>
    </div>
    <div class="divider divider--left"></div>

    <ul class="contacts">
      <li><svg viewBox="0 0 24 24"><path d="M6.6 10.8a15 15 0 0 0 6.6 6.6l2.2-2.2a1 1 0 0 1 1-.25 11.4 11.4 0 0 0 3.6.57 1 1 0 0 1 1 1V20a1 1 0 0 1-1 1A17 17 0 0 1 3 4a1 1 0 0 1 1-1h3.5a1 1 0 0 1 1 1c0 1.25.2 2.45.57 3.6a1 1 0 0 1-.25 1z"/></svg>+91 98450 21736</li>
      <li><svg viewBox="0 0 24 24"><path d="M7 1h10a2 2 0 0 1 2 2v18a2 2 0 0 1-2 2H7a2 2 0 0 1-2-2V3a2 2 0 0 1 2-2zm0 3v15h10V4z"/></svg>+91 80 4127 5590</li>
      <li><svg viewBox="0 0 24 24"><path d="M2 5h20v14H2zm2 2v.5l8 5 8-5V7z"/></svg>hello@brevlo.in</li>
    </ul>

    <div class="divider divider--right"></div>
    <p class="address">Street Name, Suite 100<br>State, Zip Code, Country</p>

    <svg class="band" viewBox="0 0 560 100" preserveAspectRatio="none" aria-hidden="true">
      <path d="M0 78 L360 64 Q372 63 380 58 L402 50 L560 50 L560 56 L404 56 L384 64 Q376 69 362 70 L0 84 Z" fill="#1a1a1a"/>
      <path d="M0 86 L366 72 Q380 71 392 62 L412 46 Q420 40 432 40 L560 40 L560 100 L0 100 Z" fill="var(--brand-red)"/>
    </svg>
    <span class="band__site">www.brevlo.in</span>
  </section>
</body>
</html>
```